Bright Harbor Counseling Letterhead for hip modern business

I would like some ombre use of the colors in the logo hip letterhead that incorporates logo colors and feel, needs to connect with young professionals and college students. i need to be able to write letters to schools to excuse absences as well. i like color blocks on one side preferably using colors from the attached logo design.

Target Market(s)

high income young people, young adults and college students

Industry/Entity Type

mental health

Font styles to use
Serif
Sans Serif

Colors
0054AA
0677BA
7BADD7
CADEEF
E8F1F8
0094D4
00A9DD
6FCCEA
C7EBF8
E9F6FB
00AB8E
00BBA5
67D7C9
C6EFE9
E9F9F6
59FF00
82FF00
B8FF75
E3FFCB
F4FFEA
A7469A
B969AE
D3A5CF
EDDBEB
F8F0F9
6B429C
8869AF
B7A5CE
E3DAEB
F3F0F8

Requirements
Must have
• a modern hip feel, somewhat color

```html
<!DOCTYPE html>
<html lang="en">
<head>
<meta charset="utf-8">
<title>Bright Harbor Counseling Letterhead</title>
<link href="https://fonts.googleapis.com/css2?family=Jost:wght@300;400&display=swap" rel="stylesheet">
<style>
  :root {
    --backdrop: #e7e4e0;
    --paper: #ffffff;
    --ink: #1d1d1f;
    --rule: #9a9a9a;
    --plum: #a7469a;
    --violet: #8869af;
    --deep-violet: #6b429c;
    --ocean: #0677ba;
    --sky: #0094d4;
    --teal: #00bba5;
  }
  * { box-sizing: border-box; margin: 0; padding: 0; }
  html, body {
    width: 1200px;
    height: 900px;
    overflow: hidden;
    background: var(--backdrop);
    font-family: "Jost", "Century Gothic", sans-serif;
    color: var(--ink);
  }
  .letterhead {
    position: absolute;
    left: 274px;
    top: 30px;
    width: 651px;
    height: 840px;
    background: var(--paper);
    box-shadow: 0 6px 18px rgba(0,0,0,0.18);
    overflow: hidden;
  }
  .brand {
    position: absolute;
    left: 34px;
    top: 72px;
    display: flex;
    align-items: flex-start;
    gap: 8px;
  }
  .brand-text {
    display: flex;
    flex-direction: column;
    align-items: flex-end;
  }
  .brand-name {
    font-weight: 300;
    font-size: 31px;
    line-height: 1;
    letter-spacing: 0.2px;
  }
  .brand-sub {
    font-weight: 300;
    font-size: 15px;
    letter-spacing: 2.4px;
    margin-top: 5px;
    margin-right: -2px;
  }
  .brand-dot {
    width: 14px;
    height: 14px;
    border-radius: 50%;
    background: var(--violet);
    margin-top: -6px;
  }
  .corner-color {
    position: absolute;
    right: 0;
    top: 0;
    width: 240px;
    height: 210px;
    background:
      radial-gradient(circle at 8% 40%, rgba(185,105,174,0.85) 0, rgba(185,105,174,0) 38%),
      radial-gradient(circle at 55% 20%, rgba(136,105,175,0.9) 0, rgba(136,105,175,0) 55%),
      radial-gradient(circle at 50% 75%, rgba(0,148,212,0.75) 0, rgba(0,148,212,0) 45%),
      radial-gradient(circle at 92% 85%, rgba(0,187,165,0.7) 0, rgba(0,187,165,0) 35%);
    border-bottom-left-radius: 100% 100%;
  }
  .footer {
    position: absolute;
    left: 104px;
    width: 443px;
    top: 780px;
    font-size: 11px;
    letter-spacing: 0.8px;
  }
  .footer-address {
    text-align: center;
    padding-bottom: 5px;
    border-bottom: 1px solid var(--rule);
  }
  .footer-contacts {
    display: flex;
    justify-content: space-between;
    margin-top: 7px;
    font-size: 10.5px;
  }
  .contact {
    display: flex;
    align-items: center;
    gap: 6px;
    white-space: nowrap;
  }
  .contact svg { width: 9px; height: 9px; flex: none; }
  .icon-phone { fill: var(--violet); }
  .icon-mail { fill: var(--ocean); }
  .icon-web { fill: var(--plum); }
</style>
</head>
<body>
  <main class="letterhead">
    <div class="brand">
      <div class="brand-text">
        <span class="brand-name">Bright Harbor</span>
        <span class="brand-sub">Counseling</span>
      </div>
      <span class="brand-dot"></span>
    </div>

    <div class="corner-color" role="img" aria-label="Overlapping soft circles in plum, violet, blue and teal brand colours"></div>

    <footer class="footer">
      <p class="footer-address">1480 Linden Crest Way Carmel, IN 46032</p>
      <div class="footer-contacts">
        <span class="contact">
          <svg class="icon-phone" viewBox="0 0 10 10"><path d="M2 0.5 L3.6 0.5 L4.2 2.8 L3.1 3.6 Q4 5.8 6.3 6.9 L7.1 5.8 L9.5 6.4 L9.5 8 Q9.5 9.5 8 9.5 Q1.5 9 0.5 2 Q0.5 0.5 2 0.5 Z"/></svg>
          +1 317 555 0148
        </span>
        <span class="contact">
          <svg class="icon-mail" viewBox="0 0 10 8"><path d="M0 0 H10 V1 L5 4.2 L0 1 Z M0 2.2 L5 5.4 L10 2.2 V8 H0 Z"/></svg>
          hello@brightharborcare.com
        </span>
        <span class="contact">
          <svg class="icon-web" viewBox="0 0 10 10"><circle cx="5" cy="5" r="5"/><path d="M2.5 3 Q4 2 5 3.5 Q4 5 5.5 6 Q6 8 4.5 8.5 Q3 7 2.5 5.5 Z M6.5 1.8 Q8 2.5 8 4 Q7 3.8 6.5 3 Z" fill="#fff"/></svg>
          www.brightharborcare.com
        </span>
      </div>
    </footer>
  </main>
</body>
</html>
```